Harborline Auto LLC

Car Dealer Customer Service
Address: 2874 Cresthaven Road, Shelbyville, TN 37162
web: www.harborlineautoxq.net
email: harborlineautoxq@mailnest.example
Phone: (931) 555-0148
Phone: (629) 555-0173

```html
<!DOCTYPE html>
<html lang="en">
<head>
<meta charset="utf-8">
<title>Harborline Auto LLC – Business Card</title>
<link href="https://fonts.googleapis.com/css2?family=Montserrat:wght@500;700&family=Arimo:wght@400&display=swap" rel="stylesheet">
<style>
  :root {
    --backdrop: #2a2624;
    --card: #1b1b1b;
    --blue: #2290cf;
    --gold: #f0b43c;
    --white: #f4f4f4;
  }
  * { margin: 0; padding: 0; box-sizing: border-box; }
  html, body { width: 1200px; height: 842px; overflow: hidden; }
  body {
    background: var(--backdrop);
    display: flex;
    align-items: center;
    justify-content: center;
    gap: 40px;
  }
  .card {
    position: relative;
    width: 540px;
    height: 309px;
    background: var(--card);
    overflow: hidden;
    box-shadow: 0 10px 30px rgba(0,0,0,0.45);
  }

  /* Back side: contact details */
  .band { position: absolute; left: 0; right: 0; background: var(--blue); }
  .band--top { top: 0; height: 12px; }
  .band--bottom { bottom: 0; height: 16px; }
  .contact {
    position: absolute;
    left: 0; right: 0; top: 62px;
    text-align: center;
    font-family: "Arimo", Arial, sans-serif;
    color: var(--white);
    font-size: 14px;
    line-height: 1.3;
  }
  .contact__name {
    font-family: "Montserrat", Arial, sans-serif;
    font-weight: 700;
    color: var(--blue);
    font-size: 18px;
    text-transform: uppercase;
    letter-spacing: 0.2px;
  }
  .contact__role { color: var(--gold); font-size: 14px; }
  .rule { width: 70px; height: 1px; background: var(--gold); margin: 8px auto; }
  .contact__label { color: var(--blue); font-weight: 700; margin-right: 4px; }

  /* Front side: brand */
  .accent { position: absolute; width: 40px; height: 88px; background: var(--blue); }
  .accent::after { content: ""; position: absolute; top: 0; bottom: 0; width: 4px; background: var(--gold); }
  .accent--left { left: 0; top: 112px; }
  .accent--left::after { right: 6px; }
  .accent--right { right: 0; top: 40px; }
  .accent--right::after { left: 6px; }
  .brand {
    position: absolute;
    left: 0; right: 0; top: 62px;
    display: flex; flex-direction: column; align-items: center;
    font-family: "Montserrat", Arial, sans-serif;
  }
  .brand__mark { width: 90px; height: 90px; border-radius: 50%; background: var(--blue); margin-bottom: 18px; }
  .brand__name { font-weight: 700; font-size: 30px; color: var(--blue); text-transform: uppercase; letter-spacing: 0.5px; }
  .brand__tagline { font-weight: 500; font-size: 13px; color: var(--gold); text-transform: uppercase; letter-spacing: 1px; margin-top: 4px; }
</style>
</head>
<body>
  <section class="card card--back">
    <div class="band band--top"></div>
    <div class="contact">
      <div class="contact__name">Marcus Delaney</div>
      <div class="contact__role">Managing Director</div>
      <div class="rule"></div>
      <div>2874 Cresthaven Road</div>
      <div>Shelbyville, TN 37162</div>
      <div class="rule"></div>
      <div><span class="contact__label">P:</span>(931) 555-0148</div>
      <div><span class="contact__label">P:</span>(629) 555-0173</div>
      <div><span class="contact__label">W:</span>www.harborlineautoxq.net</div>
      <div><span class="contact__label">E:</span>harborlineautoxq@mailnest.example</div>
    </div>
    <div class="band band--bottom"></div>
  </section>

  <section class="card card--front">
    <div class="accent accent--left"></div>
    <div class="accent accent--right"></div>
    <div class="brand">
      <div class="brand__mark"></div>
      <div class="brand__name">Harborline Auto</div>
      <div class="brand__tagline">Car Dealer Customer Service</div>
    </div>
  </section>
</body>
</html>
```